Virtual Racing Community for Runners Needs a Refreshed Web Design

We are a STARTUP. The current website consists of 3 main pages that function well; however, they are not producing the proper conversions because we need a more professional look and better execution of our great ideas.

First page: landing page that needs to be intriguing, sleek, create urgency, incorporate our call to action and most importantly get the consumer to click a button to get to second page. www.lomberun.com

Second page: sign up page that incorporates our already existing postwren form that doesn't take the viewer away from the page on incorrect form field entry. On successful completion needs to inform the viewer to check the email and confirm (possibly in spam) and open third page. http://www.lomberun.com/beta.html

Third page: preorder page that allows the user prepurchase through a well working form through "www.getparsnip.com." This interface works really well; however, the graphics and page need to really entice the viewer to buy. http://www.lomberun.com/preorder.html

And that's it!!! Simple 3 pages that function currently 95% how we want it, but really needs that creative touch to push it to the next level!

Contact us with any other questions!
Updates

Project Deadline Extended
Reason: I have provided numerous feedback and am awaiting redesigns. Have it narrowed down to 2 designers. Need time to vet with stakeholders.

Industry/Entity Type

Racing

```html
<!DOCTYPE html>
<html lang="en">
<head>
<meta charset="utf-8">
<title>Lomberun — Race on your own terms</title>
<link href="https://fonts.googleapis.com/css2?family=Bebas+Neue&family=Open+Sans:wght@300;400;600;700&display=swap" rel="stylesheet">
<style>
  :root {
    --ink: #111111;
    --brown: #7a2611;
    --orange: #d97b1a;
    --cream: #fde9c2;
    --field: #ebebeb;
    --field-line: #cfcfcf;
    --text: #444444;
    --footer: #151515;
    --white: #ffffff;
  }
  * { box-sizing: border-box; margin: 0; padding: 0; }
  html, body { width: 1200px; height: 843px; overflow: hidden; background: var(--white); }
  body { position: relative; font-family: "Open Sans", Arial, sans-serif; }

  .hero {
    position: absolute; left: 0; top: 0; width: 1200px; height: 312px;
    background: linear-gradient(100deg, #5a3424 0%, #a2542a 28%, #d98a3c 55%, #f3b45a 78%, #f8cf84 100%);
  }
  .brand {
    position: absolute; left: 607px; top: 22px;
    font-family: "Bebas Neue", sans-serif; font-size: 110px; line-height: 1;
    letter-spacing: 4px; color: var(--ink);
  }
  .tagline {
    position: absolute; left: 606px; top: 140px;
    font-family: "Bebas Neue", sans-serif; color: var(--ink); line-height: 1;
  }
  .tagline .main { display: block; font-size: 58px; letter-spacing: 0.5px; }
  .tagline .sub { display: block; font-size: 43px; letter-spacing: 1px; margin-top: 2px; }

  .signup-card {
    position: absolute; left: 110px; top: 277px; width: 980px; height: 318px;
    background: var(--white); box-shadow: 0 8px 22px rgba(0,0,0,0.14);
  }
  .card-head {
    height: 104px; background: var(--brown); display: flex; align-items: center;
  }
  .card-head .badge {
    width: 98px; height: 104px; background: var(--orange);
    display: flex; align-items: center; justify-content: center;
  }
  .card-head h1 {
    margin-left: 26px; font-size: 33px; font-weight: 300; color: var(--white); letter-spacing: 0.3px;
  }
  .card-head h1 strong { font-weight: 700; color: var(--cream); }

  .field {
    position: absolute; left: 78px; width: 381px; height: 51px;
    background: var(--field); border: 1px solid var(--field-line);
    padding-left: 15px; display: flex; align-items: center;
    font-size: 16.5px; color: var(--text);
  }
  .distance { position: absolute; left: 527px; top: 154px; color: var(--text); }
  .distance h2 { font-size: 16.5px; font-weight: 600; }
  .options { display: flex; align-items: center; margin-top: 6px; font-size: 15px; }
  .options span { display: flex; align-items: center; margin-right: 4px; }
  .options i {
    width: 12px; height: 12px; border-radius: 50%; border: 1px solid #999;
    background: radial-gradient(#eee, #bbb); margin-right: 7px; display: inline-block;
  }
  .cta {
    position: absolute; left: 527px; top: 242px; width: 379px; height: 62px;
    background: #000; color: var(--white); font-weight: 700; font-size: 16px;
    display: flex; align-items: center; justify-content: center; letter-spacing: 0.2px;
  }

  .site-footer {
    position: absolute; left: 0; top: 652px; width: 1200px; height: 191px; background: var(--footer);
  }
  .connect {
    position: absolute; left: 113px; top: 28px;
    font-family: "Bebas Neue", sans-serif; font-size: 29px; color: var(--white); letter-spacing: 0.5px;
  }
  .social { position: absolute; left: 115px; top: 71px; display: flex; gap: 20px; }
  .social span { width: 40px; height: 40px; border-radius: 50%; border: 2px solid var(--white); }
  .contact { position: absolute; left: 829px; top: 32px; color: var(--white); font-family: Arial, sans-serif; }
  .contact .row { display: flex; align-items: center; }
  .contact .address { font-size: 12.5px; line-height: 18px; margin-left: 12px; margin-top: -4px; }
  .contact .phone { font-size: 24px; color: #cfcfcf; margin-left: 12px; }
  .legal-bar {
    position: absolute; left: 0; top: 128px; width: 1200px; height: 48px; background: var(--orange);
    display: flex; align-items: center; justify-content: space-between; padding: 0 115px 0 115px;
    font-family: Arial, sans-serif; font-size: 11px; color: var(--white);
  }
</style>
</head>
<body>
  <header class="hero" role="img" aria-label="Photo of a runner's red and white shoes on a sunlit road">
    <div class="brand">LOMBERUN</div>
    <div class="tagline">
      <span class="main">RACE ON YOUR OWN TERMS</span>
      <span class="sub">WHEREVER. WHATEVER. WHENEVER.</span>
    </div>
  </header>

  <section class="signup-card">
    <div class="card-head">
      <div class="badge">
        <svg width="52" height="60" viewBox="0 0 52 60" fill="none" stroke="#fff" stroke-width="3" stroke-linecap="round" stroke-linejoin="round">
          <rect x="14" y="20" width="34" height="36" rx="4"/>
          <line x1="28" y1="32" x2="40" y2="32"/>
          <line x1="28" y1="39" x2="40" y2="39"/>
          <line x1="28" y1="46" x2="40" y2="46"/>
          <path d="M4 6 L10 2 L24 28 L22 36 L16 30 Z" fill="#d97b1a"/>
        </svg>
      </div>
      <h1>ANSWER FEW QUESTIONS. <strong>QUALIFY FOR BETA WEEK 2</strong></h1>
    </div>

    <div class="field" style="top:143px">Email Address</div>
    <div class="field" style="top:198px">How difficult is it to race on your own terms?</div>
    <div class="field" style="top:253px">How do you motivate yourself to run?</div>

    <div class="distance">
      <h2>What distance do you want for your first beta?</h2>
      <div class="options">
        <span><i></i>5K</span>
        <span><i></i>10K</span>
        <span><i></i>Half Marathon</span>
        <span><i></i>Marathon</span>
        <span><i></i>Other</span>
      </div>
    </div>

    <div class="cta">RESERVE MY BETA SPORT NOW</div>
  </section>

  <footer class="site-footer">
    <div class="connect">CONNECT WITH US</div>
    <div class="social" aria-label="Social links">
      <span></span><span></span><span></span><span></span>
    </div>
    <div class="contact">
      <div class="row">
        <svg width="32" height="32" viewBox="0 0 32 32"><circle cx="16" cy="16" r="15" fill="none" stroke="#fff" stroke-width="2"/><path d="M8 16 L16 9 L24 16 H21 V23 H18 V18 H14 V23 H11 V16 Z" fill="#fff"/></svg>
        <div class="address">48 Fenwick Lane Suite 9<br>Harlow Park, New York 104551</div>
      </div>
      <div class="row" style="margin-top:10px">
        <svg width="32" height="32" viewBox="0 0 32 32"><circle cx="16" cy="16" r="15" fill="none" stroke="#fff" stroke-width="2"/><path d="M11 8 L14 8 L15 12 L13 14 Q15 18 18 19 L20 17 L24 18 L24 21 Q23 24 20 24 Q10 22 8 12 Q8 9 11 8 Z" fill="#fff"/></svg>
        <div class="phone">012-555-0147</div>
      </div>
    </div>
    <div class="legal-bar">
      <span>© Copyright 2014 Lomberun. All Rights Reserved</span>
      <span>Policy | Terms</span>
    </div>
  </footer>
</body>
</html>
```